Millcrest PTA Website Design

We are working with Millcrest Elementary School PTA. They are a Parent Teacher Association that needs a new website design.

A Parent Teacher Association (PTA) is a volunteer organization that brings parents, teachers, and school staff together to support students and enhance their educational experience. PTAs organize fundraisers, sponsor school events, advocate for education policies, and foster stronger connections between families and schools.

Some sites to use for inspiration:

https://parentboardhub.com/demo/
https://nonprofits.kindlyfundr.com/blogs/more-great-pta-websites-you-should-copy
https://www.rvmxpta.com

Thank you for taking the time to consider designing a website for us. We are web developers based in Stockton and Los Angeles, CA, USA. Most of our projects go through the same process. Understanding this process may help you win a project with us. We custom-code all of our websites in-house. We don’t have any requirements as to what tools you use for your design, but we prefer Figma files. For any design that we label as four-stars, we send it to the client for review. The client picks the final design they want us to use. Once we complete this process, we will continue to show additional clients all the four-star sites and purchase them later. Your designs will have multiple chances to sell. For better chances of success, we ask that you follow these guidelines.

IMAGES:
If you use any images or icons in the design, we ask that you have a link to the asset so we can purchase the image/icon. Most of the designs we submit do not have the customer’s images on them unless they have some great images. Be creative; show us the feeling you are trying to portray with your image choices. Use any royalty-free site you choose. We subscribe to Adobe and mainly use their images, but we can purchase images outside of Adobe.

PLEASE NOTE: we will not submit designs to clients with watermarks on the images.

FONTS:
We ask that you identify the fonts used in the design. This can be done in a message if you want. We typically use Google Fonts and Adobe Fonts.

CONTENT:
We're always open to different content and ideas. We often submit designs with stock images so the client can see our vision. We typically take pictures after the website launch to use their images with our vision. Lorem Ipsum is fine for paragraphs, but we ask that you write the headers in correct English. We want to be able to show the vision and identify the sections of the website.

INSPIRATION:
We typically add a couple of links in the brief of websites we like to help you get started in your design.

REVISIONS:
We do not often ask for revisions of the designs unless we see something in the design that may not appeal to the client. If there are slight changes that we want to make, we do that in the development process.

FEEDBACK:
We rarely give feedback on designs during the design process. We are working on many website projects and do not have the time to provide feedback. We usually respond if your request is well thought out and asks specific questions, but a note asking “feedback, please” usually goes unanswered.

```html
<!DOCTYPE html>
<html lang="en">
<head>
<meta charset="utf-8">
<title>Millcrest PTA</title>
<link href="https://fonts.googleapis.com/css2?family=Poppins:wght@400;500;600;700&display=swap" rel="stylesheet">
<style>
  :root{
    --navy:#12226e;
    --navy-text:#0f1f66;
    --orange:#f55a00;
    --ink:#111111;
    --body:#2a2a2a;
    --date-grey:#e2e3e6;
    --white:#ffffff;
    --dot:#9aa3c4;
  }
  *{box-sizing:border-box;margin:0;padding:0}
  html,body{width:673px;height:1200px;overflow:hidden;background:var(--white)}
  body{position:relative;font-family:'Poppins',sans-serif;color:var(--body)}
  .abs{position:absolute}
  a{color:inherit;text-decoration:none}

  .site-header{position:absolute;left:0;top:0;width:673px;height:87px;background:var(--navy)}
  .brand{left:81px;top:30px;display:flex;align-items:center;gap:5px;color:var(--white);font-weight:600;font-size:9px}
  .brand-square{width:10px;height:10px;background:var(--white)}
  .school-link{left:374px;top:20px;font-size:7px;color:var(--orange);text-decoration:underline}
  .btn{display:flex;align-items:center;justify-content:center;background:var(--orange);color:var(--white);font-weight:600;font-size:8px}
  .header-cta{left:505px;top:16px;width:86px;height:26px}
  .main-nav a{position:absolute;top:56px;color:var(--white);font-weight:600;font-size:8px;white-space:nowrap}

  .photo{position:absolute}
  .hero-photo{left:60px;top:116px;width:306px;height:248px;background:linear-gradient(135deg,#7a5a45,#c9906b 45%,#d7b08e 70%,#e07a30)}
  .dots{left:192px;top:379px;display:flex;gap:7px}
  .dots span{width:5px;height:5px;border-radius:50%;background:var(--dot)}
  .dots span:first-child{background:var(--navy)}

  h2{font-weight:700;color:var(--ink);font-size:14px;line-height:1.2}
  .copy{font-size:7.4px;line-height:14.4px;color:var(--body)}
  .copy u,.copy .lnk{color:var(--navy-text);text-decoration:underline}

  .date-badge{width:34px;height:34px;background:var(--date-grey);border-top:5px solid var(--orange);display:flex;align-items:center;justify-content:center;font-size:7.5px;font-weight:600;color:var(--navy-text)}

  .carnival-photo{left:401px;top:288px;width:214px;height:128px;background:linear-gradient(160deg,#d9b13e,#c98548 40%,#6d8a3a 80%,#4a6a8a)}
  .meeting-photo{left:401px;top:485px;width:214px;height:128px;background:linear-gradient(150deg,#c9c4bb,#8b7a6a 40%,#5a6c8c 75%,#d9d6d0)}

  .give-title{left:67px;top:444px;font-size:20.5px;font-weight:700;color:var(--navy-text)}
  .section-rule{left:59px;top:675px;width:305px;height:1px;background:var(--navy)}
  .map{left:60px;top:696px;width:300px;height:213px;background:linear-gradient(135deg,#eef0f6,#e3e6ef)}

  .news a{position:absolute;left:405px;font-size:7.6px;color:var(--navy-text);white-space:nowrap}

  .site-footer{position:absolute;left:0;top:976px;width:673px;height:224px;background:var(--navy);color:var(--white)}
  .footer-brand{left:79px;top:53px}
  .footer-h{font-size:8.3px;font-weight:500;color:var(--orange)}
  .footer-item{font-size:7.4px;color:var(--white);white-space:nowrap}
  .icon{position:absolute;width:7px;height:7px}
  .card{width:14px;height:9px;background:#e9ecf4;border-radius:1px}
  .footer-rule{left:81px;top:160px;width:511px;height:1px;background:#4a5793}
  .copyright{left:0;top:187px;width:690px;text-align:center;font-size:7.4px}
</style>
</head>
<body>

<header class="site-header">
  <a class="abs brand" href="#"><span class="brand-square"></span>Millcrest PTA</a>
  <a class="abs school-link" href="#">Millcrest Elementary Website</a>
  <a class="abs btn header-cta" href="#">Contact Us</a>
  <nav class="main-nav">
    <a href="#" style="left:214px">PTA and YOU!</a>
    <a href="#" style="left:287px">Millcrest PTA Store</a>
    <a href="#" style="left:384px">PTA-Funded Programs</a>
    <a href="#" style="left:491px">Blue and White</a>
  </nav>
  <svg class="abs" style="left:583px;top:58px" width="9" height="9" viewBox="0 0 10 10">
    <circle cx="4" cy="4" r="3" fill="none" stroke="#fff" stroke-width="1.6"/>
    <line x1="6.2" y1="6.2" x2="9" y2="9" stroke="#fff" stroke-width="1.8"/>
  </svg>
</header>

<div class="photo hero-photo" role="img" aria-label="Parent and young girl building with colourful wooden blocks"></div>
<div class="abs dots"><span></span><span></span><span></span><span></span></div>

<h2 class="abs give-title">Give Back!</h2>
<p class="abs copy" style="left:66px;top:482px;width:270px">PTA works hard to provide an incredible array of programs and experiences for all our Millcrest Lions! With an operating budget of approximately $50,000 per year, your support is pivotal to ensuring all our Lions can experience field trips, monthly art lessons, STEM experiments, assemblies, drama program opportunities and more. Please join us by giving back!</p>
<a class="abs btn" href="#" style="left:67px;top:589px;width:86px;height:26px">Donate Now</a>

<div class="abs section-rule"></div>
<div class="abs map" role="img" aria-label="Street map showing the school location"></div>

<h2 class="abs" style="left:405px;top:123px">Important Dates</h2>
<div class="abs date-badge" style="left:405px;top:155px">2023</div>
<p class="abs copy" style="left:451px;top:151px;width:170px">Don't miss out on important PTA events throughout the year!&nbsp; Stay tuned for important <span class="lnk">2022-2023 dates!</span></p>
<div class="abs date-badge" style="left:405px;top:210px">2023</div>
<p class="abs copy" style="left:451px;top:205px;width:175px">Also, keep up with minimum days, vacation days and district-wide events by getting the Riverbend Unified Schools calendar <span class="lnk">here.</span></p>

<div class="photo carnival-photo" role="img" aria-label="Mother and daughter with painted faces at an outdoor carnival"></div>
<h2 class="abs" style="left:405px;top:424px">2024 Fall Carnival</h2>
<p class="abs copy" style="left:405px;top:446px;width:220px">Join the fun and support the Millcrest 6th Graders! Carnival games, tasty food, yummy treats...</p>

<div class="photo meeting-photo" role="img" aria-label="Parents, teacher and student talking in a classroom"></div>
<h2 class="abs" style="left:405px;top:622px;white-space:nowrap">PTA Membership and Meetings</h2>
<p class="abs copy" style="left:405px;top:644px;width:225px">Interested in joining?&nbsp; Joining Millcrest PTA online is as simple as a 1-2-3...or A-B-C! Join us <span class="lnk">here!!</span></p>
<p class="abs copy" style="left:405px;top:685px;width:225px">Ready to come to a meeting? Check out and download all the important documents here at the <span class="lnk">PTA General Meeting Information page.</span></p>
<a class="abs btn" href="#" style="left:405px;top:740px;width:86px;height:26px">Learn More</a>

<h2 class="abs" style="left:405px;top:805px">Recent News</h2>
<div class="news">
  <a href="#" style="top:833px">Volunteer with PTA!</a>
  <a href="#" style="top:851px">Millcrest Yearbook</a>
  <a href="#" style="top:872px">2024 Blue and white dinner and auction</a>
  <a href="#" style="top:891px">Spring Picnic</a>
</div>

<footer class="site-footer">
  <div class="abs brand footer-brand"><span class="brand-square"></span>Millcrest PTA</div>

  <div class="abs footer-h" style="left:188px;top:44px">Quick Links</div>
  <a class="abs footer-item" href="#" style="left:188px;top:66px">PTA and YOU!</a>
  <a class="abs footer-item" href="#" style="left:188px;top:82px">Millcrest PTA Store</a>
  <a class="abs footer-item" href="#" style="left:188px;top:98px">PTA-Funded Programs</a>
  <a class="abs footer-item" href="#" style="left:188px;top:113px">Blue and White</a>
  <a class="abs footer-item" href="#" style="left:188px;top:129px">Contact us</a>

  <div class="abs footer-h" style="left:344px;top:44px">Contact Us</div>
  <svg class="icon" style="left:343px;top:68px" viewBox="0 0 10 10"><path d="M5 0a3.6 3.6 0 0 0-3.6 3.6C1.4 6.3 5 10 5 10s3.6-3.7 3.6-6.4A3.6 3.6 0 0 0 5 0zm0 5a1.4 1.4 0 1 1 0-2.8A1.4 1.4 0 0 1 5 5z" fill="#f55a00"/></svg>
  <div class="abs footer-item" style="left:355px;top:66px">1450 Orchard Glen Place</div>
  <div class="abs footer-item" style="left:355px;top:82px">Fairhaven, CA 95399</div>
  <svg class="icon" style="left:343px;top:103px" viewBox="0 0 10 10"><path d="M2.2 0.6 3.9 2.9 3 4.2c.7 1.3 1.6 2.2 2.8 2.8l1.3-.9 2.3 1.7-.9 1.8C4.2 9.4.6 5.8.4 1.5z" fill="#f55a00"/></svg>
  <div class="abs footer-item" style="left:355px;top:102px">(555)014-2736</div>
  <svg class="icon" style="left:343px;top:123px" viewBox="0 0 10 10"><rect x="0" y="1.5" width="10" height="7" fill="#f55a00"/><path d="M0 1.8 5 5.5 10 1.8" fill="none" stroke="#12226e" stroke-width="0.9"/></svg>
  <div class="abs footer-item" style="left:355px;top:122px">millcrestlionspta@mailbox.org</div>

  <div class="abs footer-h" style="left:538px;top:44px">Social Media</div>
  <span class="icon" style="left:538px;top:68px;background:var(--orange);border-radius:50%"></span>
  <div class="abs footer-item" style="left:549px;top:66px">Friendspace</div>
  <span class="icon" style="left:538px;top:84px;background:var(--orange);border-radius:50%"></span>
  <div class="abs footer-item" style="left:549px;top:82px">Snapgallery</div>
  <span class="icon" style="left:538px;top:100px;background:var(--orange);border-radius:50%"></span>
  <div class="abs footer-item" style="left:549px;top:98px">Workline</div>
  <div class="abs" style="left:536px;top:127px;display:flex;gap:3px">
    <span class="card"></span><span class="card"></span><span class="card"></span><span class="card"></span><span class="card"></span><span class="card"></span>
  </div>

  <div class="abs footer-rule"></div>
  <div class="abs footer-item copyright">Copyright@2025.All Rights Reserved.</div>
</footer>

</body>
</html>
```